Ridgeline Haul Carriers - Website

A clean, not cluttered informative website for our business. We specialize in the transportation of radioactive materials across North America. The site is mostly for information about our company and will not be used to attract business but will be used to attract employee's mainly drivers. Driver's are very hard to find in our area. One of the pages needs to be a job's posting page with an apply now button. Either an application can be filled out there or a resume can be uploaded which ever functionality works better. I would like a website that I can easily edit, ability to change text and photos.

Number of Pages Required

5+ page

Colors

Designer to choose colors to be used in the design.

Requirements
Must have
• Home - About - Services - Jobs - Contact pages
• A way prospective employee's can apply or upload their resume to be emailed to me
• Very clean apperance
Should not have
• I don't want it to be busy

```html
<!DOCTYPE html>
<html lang="en">
<head>
<meta charset="utf-8">
<title>Ridgeline Haul Carriers</title>
<link href="https://fonts.googleapis.com/css2?family=Arimo:wght@400;700&family=Open+Sans:wght@700;800&display=swap" rel="stylesheet">
<style>
:root{
  --red:#b8000b;
  --red-dark:#9d0008;
  --ink:#222222;
  --text:#3a3a3a;
  --muted:#555555;
  --panel:#efefef;
  --line:#cfcfcf;
  --white:#ffffff;
  --footer-bar:#333333;
}
*{box-sizing:border-box;margin:0;padding:0}
html,body{width:1200px;height:2655px;overflow:hidden;background:var(--white)}
body{position:relative;font-family:"Arimo",Arial,sans-serif;color:var(--text)}
.abs{position:absolute}

/* header */
.site-header{position:absolute;left:0;top:0;width:1200px;height:110px;background:var(--white)}
.brand{position:absolute;left:74px;top:36px;font-family:"Open Sans",sans-serif;font-weight:800;font-size:27px;color:var(--red);letter-spacing:.5px;text-transform:uppercase}
.main-nav{position:absolute;top:47px;left:0;width:1200px;font-size:14px;font-weight:700;color:var(--ink);letter-spacing:.3px}
.main-nav a{position:absolute;color:inherit;text-decoration:none;white-space:nowrap}
.main-nav a.is-active{color:var(--red)}

/* hero */
.hero{position:absolute;left:0;top:110px;width:1200px;height:555px;background:linear-gradient(180deg,#8d8f92 0%,#6b6d70 40%,#4a4b4d 75%,#3d3e40 100%)}
.hero-title{position:absolute;left:0;top:215px;width:1200px;text-align:center;font-family:"Open Sans",sans-serif;font-weight:700;font-size:56px;line-height:58px;color:var(--white);text-transform:uppercase}
.hero-title .accent{color:var(--red)}
.slider-dots{position:absolute;top:506px;left:560px;display:flex;gap:8px}
.slider-dots span{width:12px;height:12px;border-radius:50%;background:var(--white)}
.slider-dots span.is-active{background:var(--red)}

/* buttons */
.btn{position:absolute;display:flex;align-items:center;justify-content:center;background:var(--red);color:var(--white);font-weight:700;font-size:15px;letter-spacing:.3px;text-transform:uppercase}

/* about */
.section-title{position:absolute;font-weight:700;font-size:27px;color:var(--ink);text-transform:uppercase}
.about-title{left:0;top:717px;width:1200px;text-align:center}
.about-copy{position:absolute;left:100px;width:1000px;text-align:center;font-size:17px;line-height:34px;color:var(--text)}
.mission-title{position:absolute;left:0;top:883px;width:1200px;text-align:center;font-size:20px;font-weight:700;color:var(--red);text-transform:uppercase}

/* service */
.service{position:absolute;left:0;top:1154px;width:1200px;height:405px;background:var(--panel)}
.service-photo{position:absolute;left:0;top:0;width:584px;height:405px;background:linear-gradient(135deg,#6e7480 0%,#8c2a2e 45%,#3b2a2c 75%,#d9a06a 100%);clip-path:polygon(0 0,543px 0,584px 100%,0 100%)}
.service-title{left:614px;top:50px;font-size:26px}
.service-copy{position:absolute;left:614px;top:108px;width:530px;font-size:15.5px;line-height:30.5px;color:var(--text)}

/* jobs */
.jobs-title{position:absolute;left:0;top:1605px;width:1200px;text-align:center;font-family:"Open Sans",sans-serif;font-weight:700;font-size:28px;color:var(--ink)}
.job-photo{position:absolute;top:1676px;width:211px;height:188px}
.job-heading{position:absolute;top:1674px;font-size:20px;font-weight:700;color:var(--red);text-transform:uppercase}
.job-copy{position:absolute;top:1707px;width:280px;font-size:14px;line-height:24px;color:var(--text)}

/* contact */
.contact{position:absolute;left:0;top:1950px;width:1200px;height:355px;background:var(--panel)}
.contact-photo{position:absolute;left:0;top:0;width:497px;height:355px;background:radial-gradient(circle at 18% 68%,#f3c27a 0%,#c5653a 18%,#4b3a3a 48%,#1f2226 100%)}
.contact-title{left:524px;top:57px;font-size:27px}
.field{position:absolute;background:var(--white);border:1px solid var(--line);font-size:13px;color:var(--muted);padding:12px 15px}
.submit{position:absolute;left:832px;top:254px;width:294px;height:39px;background:var(--red);color:var(--white);font-weight:700;font-size:16px;display:flex;align-items:center;justify-content:center;letter-spacing:.5px}

/* footer */
.footer-heading{position:absolute;top:2358px;font-size:15px;font-weight:700;color:var(--ink);text-transform:uppercase}
.footer-text{position:absolute;font-size:14px;line-height:21px;color:var(--text)}
.footer-text .sep{margin:0 14px}
.footer-name{color:var(--red);font-weight:700}
.contact-line{position:absolute;left:373px;font-size:14px;color:var(--text);display:flex;align-items:center;gap:10px}
.social{position:absolute;left:74px;top:2496px;display:flex;gap:18px}
.social span{width:20px;height:20px;border-radius:50%;background:#7d7d7d}
.newsletter-input{position:absolute;left:885px;top:2393px;width:241px;height:43px;border:1px solid var(--line);font-size:12px;color:var(--muted);padding:14px 14px}
.newsletter-btn{position:absolute;left:1051px;top:2448px;width:75px;height:30px;background:var(--red);color:var(--white);font-size:12px;font-weight:700;display:flex;align-items:center;justify-content:center}
.copyright{position:absolute;left:0;top:2593px;width:1200px;height:62px;background:var(--footer-bar);color:var(--white);font-size:12.5px;display:flex;align-items:center;justify-content:center}
</style>
</head>
<body>

<header class="site-header">
  <div class="brand">Ridgeline Haul Carriers</div>
  <nav class="main-nav">
    <a class="is-active" style="left:600px">HOME</a>
    <a style="left:706px">ABOUT</a>
    <a style="left:819px">SERVICES</a>
    <a style="left:955px">JOBS</a>
    <a style="left:1057px">CONTACT</a>
  </nav>
</header>

<section class="hero" role="img" aria-label="Photo of a tractor trailer hauling secured cargo containers outside a brick depot">
  <h1 class="hero-title">Welcome to<br><span class="accent">Ridgeline Haul</span> Carriers</h1>
  <div class="slider-dots"><span class="is-active"></span><span></span><span></span><span></span></div>
</section>

<section>
  <h2 class="section-title about-title">About Our Company</h2>
  <p class="about-copy" style="top:766px">Crestway Express has been providing quality transportation services since our founding in 1999.<br>Crestway Express is part of the Crestway Group of Companies. The Crestway Group consists of Crestway Express, Crestway Freight, Crestway Equipment Leasing, Crestway Logistics and Crestway Holdings.</p>
  <h3 class="mission-title">Our Mission</h3>
  <p class="about-copy" style="top:916px">With a firm commitment to superior service and integrity above all, the Crestway team has developed an enviable reputation within the transportation industry.</p>
  <div class="btn" style="left:519px;top:1023px;width:164px;height:50px">Read More</div>
</section>

<section class="service">
  <div class="service-photo" role="img" aria-label="Photo of a red tanker truck driving on a highway at sunset"></div>
  <h2 class="section-title service-title">Our Service</h2>
  <p class="service-copy">At Crestway Express, we specialize in both expedited and regular LTL, Partial Load and Full Truck Load service between Canada, the USA. and Mexico. In addition, to meet our just in time door to door service requirements, our policy includes one line hauls right to your delivery, which eliminates extra handling of your products which also in turn reduces damages and claims.</p>
  <div class="btn" style="left:614px;top:292px;width:165px;height:48px">Read More</div>
</section>

<section>
  <h2 class="jobs-title">JOBS</h2>
  <div class="job-photo" style="left:74px;background:linear-gradient(160deg,#b9c6d3 0%,#8e9aa6 45%,#c4472f 70%,#5b6470 100%)" role="img" aria-label="Photo of an owner operator on the phone beside his truck"></div>
  <h3 class="job-heading" style="left:303px">Owner/Operators</h3>
  <p class="job-copy" style="left:303px">Sed accumsan sollicitudin sapien, sit amet adipiscing turpis gravida eget turpis vehicula tempus..</p>
  <div class="btn" style="left:312px;top:1816px;width:164px;height:48px">Apply Now</div>

  <div class="job-photo" style="left:614px;background:linear-gradient(150deg,#9aa3ad 0%,#4a4f57 45%,#b3262b 70%,#7e8690 100%)" role="img" aria-label="Photo of a company driver standing beside a red truck cab"></div>
  <h3 class="job-heading" style="left:843px">Company Drivers</h3>
  <p class="job-copy" style="left:843px">Sed accumsan sollicitudin sapien, sit amet adipiscing turpis gravida eget turpis vehicula tempus..</p>
  <div class="btn" style="left:851px;top:1816px;width:165px;height:48px">Apply Now</div>
</section>

<section class="contact">
  <div class="contact-photo" role="img" aria-label="Photo of a chrome tanker truck at sunrise"></div>
  <h2 class="section-title contact-title">Contact Us</h2>
  <div class="field" style="left:524px;top:108px;width:294px;height:41px">Name</div>
  <div class="field" style="left:524px;top:156px;width:294px;height:41px">Email Address</div>
  <div class="field" style="left:524px;top:204px;width:294px;height:41px">Phone No</div>
  <div class="field" style="left:524px;top:252px;width:294px;height:41px">Subject</div>
  <div class="field" style="left:832px;top:108px;width:294px;height:137px">Message</div>
  <div class="submit">SUBMIT</div>
</section>

<footer>
  <h4 class="footer-heading" style="left:74px">Site Map</h4>
  <p class="footer-text" style="left:74px;top:2386px">Home<span class="sep">/</span>About<span class="sep">/</span>Services</p>
  <p class="footer-text" style="left:74px;top:2413px">Job<span class="sep">/</span>Contact</p>
  <h4 class="footer-heading" style="left:74px;top:2463px">Follow Us</h4>
  <div class="social"><span></span><span></span><span></span><span></span><span></span><span></span></div>

  <h4 class="footer-heading" style="left:373px">Contact Info</h4>
  <p class="footer-text" style="left:373px;top:2386px"><span class="footer-name">Ridgeline Haul Carriers</span><br>4180 Alder Bend Road, Reno,<br>NV 89502 Interstate<br>80 EXIT #14</p>
  <div class="contact-line" style="top:2482px">
    <svg width="12" height="12" viewBox="0 0 24 24"><path fill="#555" d="M6.6 10.8a15.1 15.1 0 0 0 6.6 6.6l2.2-2.2a1 1 0 0 1 1-.25 11.4 11.4 0 0 0 3.6.57 1 1 0 0 1 1 1V20a1 1 0 0 1-1 1A17 17 0 0 1 3 4a1 1 0 0 1 1-1h3.5a1 1 0 0 1 1 1c0 1.25.2 2.45.57 3.57a1 1 0 0 1-.25 1z"/></svg>
    (555) 014-2287</div>
  <div class="contact-line" style="top:2512px">
    <svg width="13" height="11" viewBox="0 0 26 20"><rect width="26" height="20" rx="2" fill="#555"/><path d="M2 3l11 8 11-8" stroke="#fff" stroke-width="2" fill="none"/></svg>
    hello@ridgelinehaul.com</div>

  <h4 class="footer-heading" style="left:648px">Resources</h4>
  <p class="footer-text" style="left:648px;top:2389px;line-height:23px">Fusce at sollicitudin neque<br>Etiam bibendum<br>Lacus at euismod<br>Convallis</p>

  <h4 class="footer-heading" style="left:885px">Newsletter Sign Up</h4>
  <div class="newsletter-input">Enter Email Address</div>
  <div class="newsletter-btn">SIGN UP</div>

  <div class="copyright">Copyright © 2019. Company Name. All Right Reserved</div>
</footer>

</body>
</html>
```